A wine Label for a new brand of New Zealand Wine

We are looking for a Wine Label for our "Harbor Pine" brand of wines from North Otago New Zealand. We would like the label to perhaps use the HP as a logo and the rest up to the designer. We have our vineyards located in the Waitaki Valley New Zealand which is a southern region with mountains and a river flowing past our vineyard. Photos attached of Dramatic Landscape. Also attached is a basic outline of requirements for the front bottle of the label. The rear bottle label will contain writing about the wines background plus statutory regulations on Alc. Vol, bar code etc. Front Label size to be no Larger than 80mm deep by 100 mm wide. The label can be simple or graphic, whatever the designer chooses.
Target Market(s)
New Wine Brand
Look and feel
Each slider illustrates characteristics of the customer's brand and the style your logo design should communicate.

```html
<!DOCTYPE html>
<html lang="en">
<head>
<meta charset="utf-8">
<title>Harbor Pine — Pinot Gris Labels</title>
<link href="https://fonts.googleapis.com/css2?family=Cormorant+Garamond:wght@400;500;600&family=Lato:wght@400;700&display=swap" rel="stylesheet">
<style>
  :root {
    --backdrop: #e9eef1;
    --paper: #fbfbf8;
    --gold: #b08a3e;
    --ink: #3a3a38;
    --ink-soft: #6d6d68;
    --green-light: #b9dcbf;
    --green-deep: #2f8a55;
    --earth-light: #e3d7bd;
    --earth-deep: #8a6f45;
    --badge: #2e3a33;
  }
  * { margin: 0; padding: 0; box-sizing: border-box; }
  html, body { width: 786px; height: 1200px; overflow: hidden; }
  body {
    background: var(--backdrop);
    font-family: "Cormorant Garamond", Georgia, serif;
    color: var(--ink);
    position: relative;
  }
  .label {
    position: absolute;
    width: 340px;
    height: 480px;
    background: var(--paper);
    box-shadow: 0 2px 10px rgba(40, 55, 65, 0.12);
    overflow: hidden;
  }
  .label--green { left: 35px; top: 70px; }
  .label--earth { left: 411px; top: 70px; }
  .label--back { left: 223px; top: 650px; }

  .brand {
    position: absolute;
    top: 54px; left: 0; right: 0;
    display: flex; align-items: center; justify-content: center; gap: 10px;
  }
  .brand__mark { width: 22px; height: 22px; background: var(--gold); }
  .brand__name {
    font-weight: 600; font-size: 22px; letter-spacing: 2px;
    text-transform: uppercase; color: var(--gold); line-height: 1;
  }
  .varietal {
    position: absolute; top: 140px; left: 0; right: 0;
    text-align: center; font-size: 34px; font-weight: 500;
    letter-spacing: 4px; color: var(--ink); line-height: 1.1;
  }
  .vintage {
    position: absolute; top: 188px; left: 0; right: 0;
    text-align: center; font-size: 18px; letter-spacing: 3px; color: var(--ink);
  }
  .region {
    position: absolute; top: 224px; left: 0; right: 0;
    text-align: center; font-size: 16px; font-style: italic; color: var(--ink-soft);
  }
  .landscape {
    position: absolute; left: 0; right: 0; bottom: 0; height: 190px;
  }
  .label--green .landscape {
    background: linear-gradient(to bottom, var(--green-light), var(--green-deep));
  }
  .label--earth .landscape {
    background: linear-gradient(to bottom, var(--earth-light), var(--earth-deep));
  }
  .origin {
    position: absolute; bottom: 12px; left: 0; right: 0; text-align: center;
    font-family: "Lato", Arial, sans-serif; font-size: 8px; letter-spacing: 2px;
    text-transform: uppercase; color: #ffffff;
  }

  .back__copy {
    position: absolute; top: 40px; left: 36px; right: 36px;
    font-family: "Lato", Arial, sans-serif; font-size: 11px; line-height: 1.6;
    color: var(--ink-soft); text-align: justify;
  }
  .back__copy p + p { margin-top: 12px; }
  .back__brand {
    position: absolute; top: 232px; left: 36px;
    font-size: 22px; font-weight: 600; letter-spacing: 2px;
    text-transform: uppercase; color: var(--gold); line-height: 1;
  }
  .back__badge {
    position: absolute; top: 226px; right: 40px;
    width: 38px; height: 38px; border-radius: 50%; background: var(--badge);
  }
  .back__facts {
    position: absolute; bottom: 40px; left: 36px;
    font-family: "Lato", Arial, sans-serif; font-size: 10px; line-height: 1.7;
    color: var(--ink-soft);
  }
  .back__icons { position: absolute; bottom: 44px; right: 40px; display: flex; gap: 8px; }
  .back__icons svg { width: 22px; height: 22px; display: block; }
</style>
</head>
<body>

  <section class="label label--green">
    <div class="brand"><span class="brand__mark"></span><span class="brand__name">Harbor Pine</span></div>
    <h1 class="varietal">PINOT GRIS</h1>
    <div class="vintage">2015</div>
    <div class="region">Waitaki Valley</div>
    <div class="landscape" role="img" aria-label="Layered green valley hills landscape artwork"></div>
    <div class="origin">New Zealand Wine</div>
  </section>

  <section class="label label--earth">
    <div class="brand"><span class="brand__mark"></span><span class="brand__name">Harbor Pine</span></div>
    <h1 class="varietal">PINOT GRIS</h1>
    <div class="vintage">2015</div>
    <div class="region">Waitaki Valley</div>
    <div class="landscape" role="img" aria-label="Layered golden-brown valley hills landscape artwork"></div>
    <div class="origin">New Zealand Wine</div>
  </section>

  <section class="label label--back">
    <div class="back__copy">
      <p>Our vines grow on the gravel terraces of the Waitaki Valley, where cool mountain air and long summer days shape wines of purity and quiet depth.</p>
      <p>This Pinot Gris offers ripe pear, white blossom and a gentle spice, finishing crisp and long. Enjoy chilled with seafood or light dishes.</p>
    </div>
    <div class="back__brand">Harbor Pine</div>
    <div class="back__badge" role="img" aria-label="Regional certification badge"></div>
    <div class="back__facts">
      <div>Produce of New Zealand</div>
      <div>750ml</div>
      <div>12.5% vol</div>
    </div>
    <div class="back__icons">
      <svg viewBox="0 0 22 22" aria-hidden="true"><rect x="1" y="1" width="20" height="20" fill="none" stroke="var(--ink-soft)" stroke-width="1.2"/><circle cx="11" cy="11" r="5" fill="none" stroke="var(--ink-soft)" stroke-width="1.2"/><line x1="4" y1="18" x2="18" y2="4" stroke="var(--ink-soft)" stroke-width="1.2"/></svg>
      <svg viewBox="0 0 22 22" aria-hidden="true"><rect x="1" y="1" width="20" height="20" fill="none" stroke="var(--ink-soft)" stroke-width="1.2"/><path d="M8 5 L14 5 L14 9 C14 12 8 12 8 9 Z" fill="none" stroke="var(--ink-soft)" stroke-width="1.2"/><line x1="11" y1="12" x2="11" y2="17" stroke="var(--ink-soft)" stroke-width="1.2"/><line x1="4" y1="18" x2="18" y2="4" stroke="var(--ink-soft)" stroke-width="1.2"/></svg>
    </div>
  </section>

</body>
</html>
```